Webdesign für Industrieanlagenbau-Unternehmen
Zielgruppe
Die KLR services GmbH ist ein ein österreichisches, eigentümergeführtes Industrieanlagenbau-Unternehmen mit Niederlassungen an derzeit 2 Standorten (Steinbrunn/NÖ und Almfeld/Sbg) und ist in den Geschäftsfeldern Industrieanlagenbau, Reinraumtechnik und Sondermaschinenbau - sowie im Projekt- und Behördenmanagement tätig.
Die KLR services GmbH unterstützt ihre B2B-Kunden bei der Umsetzung von Engineering-Projekten in der Hightech-, Elektronik- und Prozessindustrie.
Unsere Kernkompetenzen sind Konzepterstellung, 3D-Planung, Konstruktion, Design und Montage von Prozessanlagen und Reinräumen, eine eigene Fertigung und Prototypenbau in unserer „Werkhalle Quellbach“ sowie die Abwicklung des Behörden-Managements wie z.B. Einreichverfahren nach Gewerbeordnung.
Langjährige und dauerhafte Geschäftsbeziehungen zu unseren Kunden stehen bei uns im Vordergrund.
Zielsgruppe der neuen website:
„Visitenkarte“ der KLR services GmbH
potentielle Mitarbeiter („Employer Branding“), Ingenieure/Projektmanager (WI-Maschinenbau, Elektro- und Prozesstechnik), Mechatroniker, Schlosser, Elektriker
B2B Kunden aus Bereichen Mikroelektronik-Fertigung, chemische Industrie, Lebensmittel- und Pharmaproduktion
Bestandskunden (Stakeholder des „Buying Centers“ bei Kunden)
Neukunden „eingeschränkt“ (dzt. Keine aktive Kundenakquise via web geplant)
Aufgabenstellung
Allgemeine Anforderungen an die neue website:
Ziel sind eher „schlanke“ Texte & Design (vgl. https://www.varnhold-gruppe.com/de/)
Produkt- und Leistungsspezifisches Bildmaterial sollen hauptsächlich KLR-eigene Fotos und Videos sein (Stock-Fotos nur für Allgemeine Bilder). Beispielhaftes Bildmaterial (sollte durch KLR Mitarbeiter dann im CMS einfach ausgetauscht werden können) in diesen Unterlagen
CMS (Content Management System) zur Administration durch KLR Mitarbeiter
Hosting auf europäischen ServernServern (z.B. https://serverkiste-demo.com/, https://www.datenfeld-demo.com, https://www.rechenhof-demo.de, https://www.netzquelle-demo.com/, https://www.zuvo-demo.at)
Basierend auf weitverbreiteten open-Source Systemen (z.B. Wordpress , Joomla, TYPO3)
Responsive Webdesign – eine Website für alle Geräte (PC, Tablet, Smartphone) und alle gängigen Browser (Chrome, Edge, Safari, Firefox, Opera, Internet Explorer)
Google Pagespeed mind. 85 Punkte, GTmetrix Grade > 80%
Sicherheitszertifikat (SSL-Zertifikat)
Sprache – Deutsch, Englisch
E-Commerce-Gesetz (ECG) & DSGVO konform (Cookie Disclaimer Standard „nur notwendige“)
Impressum
AGB - Allgemeine Lieferungs- und Zahlungsbedingungen
Sitemap
Vollständige Rechte an der website (Design, Inhalt etc.) bei KLR services GmbH
Einbettung von Text, Fotos und Videos durch KLR Mitarbeiter
Hinzufügen von Menü-Unterpunkten durch KLR Mitarbeiter

```html
<!DOCTYPE html>
<html lang="de">
<head>
<meta charset="utf-8">
<title>KLR Services GmbH – Wir bauen Ihre Anlagen</title>
<link href="https://fonts.googleapis.com/css2?family=Open+Sans:wght@400;600;700&display=swap" rel="stylesheet">
<style>
:root{
  --red:#d9251d;
  --text:#3a3a3a;
  --dark:#2b2b2b;
  --bg:#f5f5f5;
  --band:#ececec;
  --navy:#0f1f2e;
  --white:#ffffff;
}
*{margin:0;padding:0;box-sizing:border-box}
html,body{width:1200px;height:3175px;overflow:hidden}
body{font-family:"Open Sans",Arial,sans-serif;color:var(--text);background:var(--bg);font-size:16px;line-height:1.5}
.site-header{height:131px;display:flex;align-items:center;justify-content:space-between;padding:0 75px;background:var(--bg)}
.brand{font-weight:700;font-size:46px;color:var(--red);letter-spacing:1px;display:flex;align-items:center;gap:12px}
.brand-square{width:36px;height:40px;background:var(--red);border-radius:4px}
.main-nav{display:flex;gap:48px;font-weight:600;font-size:18px}
.main-nav a{color:var(--dark);text-decoration:none}
.main-nav a.active{color:var(--red)}
.hero{height:319px;position:relative;display:flex;align-items:center;justify-content:center}
.hero-image{position:absolute;inset:0;background:linear-gradient(135deg,#3b4d63 0%,#8a9bae 35%,#c5ced8 55%,#6e7f93 80%,#2f4057 100%)}
.hero h1{position:relative;color:var(--white);font-size:58px;font-weight:600;text-shadow:0 2px 6px rgba(0,0,0,.35)}
.intro{height:416px;padding-top:87px;text-align:center;font-size:16px;line-height:24.5px}
.intro p{width:900px;margin:0 auto 24px}
.intro strong{font-weight:700;color:var(--dark)}
.clients{height:522px;background:var(--band);text-align:center;padding-top:64px}
.section-title{color:var(--red);font-size:28px;font-weight:600;line-height:36px}
.section-lead{width:780px;margin:2px auto 0;font-size:16px;line-height:24.5px}
.client-grid{display:grid;grid-template-columns:repeat(4,1fr);width:1050px;margin:56px auto 0;row-gap:92px}
.client{display:flex;align-items:center;justify-content:center;gap:10px;font-weight:700;font-size:30px;height:44px;white-space:nowrap}
.client .dot{width:26px;height:26px;border-radius:50%;flex:none}
.client.small{font-size:22px}
.c-blue{color:#1b3a9c}.c-navy{color:#1d2a3a}.c-teal{color:#1f5f9a}.c-grey{color:#8e8e8e}.c-sky{color:#1a9ad6}
.goal{height:522px;display:flex;align-items:center;padding-left:142px}
.goal-visual{width:320px;height:308px;background:linear-gradient(160deg,#e6ecf3,#9fb3cc);border-radius:4px}
.goal-text{margin-left:107px;width:470px}
.goal-text h2{color:var(--red);font-size:24px;font-weight:600;line-height:28px;margin-bottom:18px}
.goal-text p{font-size:16px;line-height:24.5px}
.team{height:931px;background:var(--band);text-align:center;padding-top:80px}
.team-grid{display:grid;grid-template-columns:repeat(4,266px);margin:50px 0 0 68px;row-gap:52px}
.member{display:flex;flex-direction:column;align-items:center}
.avatar{width:108px;height:108px;border-radius:50%;background:linear-gradient(180deg,#c9c9c9,#8d8d8d);margin-bottom:8px;overflow:hidden}
.member .name{font-weight:700;font-size:15px;line-height:20px;color:var(--dark)}
.member .role{font-size:15px;line-height:20px}
.site-footer{height:334px;background:var(--navy);color:var(--white);position:relative;font-size:14px}
.footer-col{position:absolute;top:42px}
.footer-col h3{color:var(--red);font-size:16px;font-weight:600;margin-bottom:6px}
.footer-col li{list-style:none;line-height:22px}
.footer-brand{position:absolute;left:918px;top:38px;font-size:13px;line-height:19px}
.footer-brand .brand{color:var(--white);font-size:42px;margin-bottom:20px}
.footer-brand .brand-square{background:var(--white);width:32px;height:36px}
.footer-brand strong{font-weight:700}
.footer-brand p{margin:0 0 14px 6px;font-weight:600}
.footer-bottom{position:absolute;left:75px;top:303px;font-size:11px;font-weight:600;display:flex;color:#cfd4da}
.footer-bottom span{margin-right:44px}
.footer-bottom a{color:#cfd4da;margin-right:60px}
</style>
</head>
<body>
<header class="site-header">
  <div class="brand"><span class="brand-square"></span>KLR</div>
  <nav class="main-nav">
    <a class="active" href="#">Home</a><a href="#">Leistungen</a><a href="#">Jobs/Karriere</a><a href="#">Kontakt</a><a href="#">Kunden-Portal</a>
  </nav>
</header>

<section class="hero">
  <div class="hero-image" role="img" aria-label="Industrieanlage mit glänzenden Rohrleitungen und Lüftungskanälen"></div>
  <h1>Wir bauen Ihre Anlagen.</h1>
</section>

<section class="intro">
  <p><strong>Die KLR Services GmbH</strong> ist ein österreichisches Industrieanlagenbau-Unternehmen und unterstützt Sie bei der Umsetzung von Engineering-Projekten in der Hightech-, Elektronik- und Prozessindustrie. Unsere Kernkompetenzen sind Konzepterstellung, 3D-Planung, Konstruktion, Design und Montage von Prozessanlagen und Reinräumen.</p>
  <p>Wir betreiben eine eigene Fertigung und Prototypenbau in unserer „Werkhalle Quellbach“ und unterhalten einen eigenen Fuhrpark für unsere Montageteams. Abhängig von der Projektgröße sichern wir als Generalunternehmer (GU) die effiziente Ausführung Ihres Vorhabens und setzen das Projekt vollständig um – „Fire &amp; Forget“.<br>Wir übernehmen auch die Abwicklung des Behörden-Managements wie z.B. Einreichverfahren nach Gewerbeordnung (GewO). Langfristige, verlässliche und vertrauensvolle Geschäftsbeziehungen zu unseren Kunden stehen bei uns im Vordergrund.</p>
</section>

<section class="clients">
  <h2 class="section-title">Unsere Kunden</h2>
  <p class="section-lead">Unsere Kunden sind in den Geschäftsfeldern Industrieanlagenbau, Reinraumtechnik und Sondermaschinenbau tätig. Wir liefern schlüsselfertige Industrieanlagen, projektspezifische Lösungen und bieten Unterstützung bei Behördenverfahren und im Projekt- und Prozessmanagement</p>
  <div class="client-grid">
    <div class="client c-blue">Norvalt</div>
    <div class="client c-navy">Brenholm</div>
    <div class="client c-teal">Calvera</div>
    <div class="client small c-teal"><span class="dot" style="background:#1f5f9a"></span>Quintel Nanotech</div>
    <div class="client small c-blue">Halden-Technik</div>
    <div class="client c-sky">Vireda</div>
    <div class="client c-grey">Ostrak</div>
    <div class="client c-sky">Lumira</div>
  </div>
</section>

<section class="goal">
  <div class="goal-visual" role="img" aria-label="Illustration: Ingenieur mit Tablet vor Gebäude, Taschenrechner und Zahnrad"></div>
  <div class="goal-text">
    <h2>Unser Ziel ist, die Erwartungen und Anforderungen unserer Kunden zu erfüllen und zu übertreffen</h2>
    <p>Das erreichen wir durch das Finden kosteneffizienter, innovativer Lösungen und der Schaffung eines beidseitigen Vertrauensverhältnisses auf persönlicher Ebene mit unseren Kunden. Wir haben höchste Qualitätsansprüche und sind ein verlässlicher Problemlöser.</p>
  </div>
</section>

<section class="team">
  <h2 class="section-title">Unser Team</h2>
  <p class="section-lead" style="width:720px">Unsere Engineering- und Montageteams arbeiten selbstständig, abteilungsübergreifend und strukturiert. Kreativität und „Hands-On“ Mentalität zeichnen unsere Mitarbeiter*innen aus.</p>
  <div class="team-grid">
    <div class="member"><div class="avatar" role="img" aria-label="Porträtfoto"></div><div class="name">DI Lukas Hanner, MBA</div><div class="role">CEO</div></div>
    <div class="member"><div class="avatar" role="img" aria-label="Porträtfoto"></div><div class="name">DI Florian Weixler</div><div class="role">Project Manager</div></div>
    <div class="member"><div class="avatar" role="img" aria-label="Porträtfoto"></div><div class="name">DI Stefan Brandl</div><div class="role">Head of Mechanical Engineering</div></div>
    <div class="member"><div class="avatar" role="img" aria-label="Porträtfoto"></div><div class="name">Mag. Katrin Ostler</div><div class="role">Finance &amp; Controlling, HR</div></div>
    <div class="member"><div class="avatar" role="img" aria-label="Porträtfoto"></div><div class="name">Dipl. BW Rainer Bastow</div><div class="role">Projekt Manager</div></div>
    <div class="member"><div class="avatar" role="img" aria-label="Porträtfoto"></div><div class="name">Goran Vukelic</div><div class="role">Project Engineer</div></div>
    <div class="member"><svg class="avatar" viewBox="0 0 108 108" style="background:#c8c8c8" aria-label="Platzhalter ohne Foto"><circle cx="54" cy="40" r="20" fill="none" stroke="#d9251d" stroke-width="6"/><path d="M14 96a44 30 0 0 1 80 0" fill="none" stroke="#d9251d" stroke-width="6"/></svg><div class="name">Anton Riedlmair</div><div class="role">Engineering</div></div>
    <div class="member"><div class="avatar" role="img" aria-label="Porträtfoto"></div><div class="name">Daniel Farahmand, B.Eng</div><div class="role">Electrical Engineerng / MSRT</div></div>
    <div class="member"><div class="avatar" role="img" aria-label="Porträtfoto"></div><div class="name">Markus Ledl</div><div class="role">Head of Assembly / Leiter Montage</div></div>
    <div class="member"><div class="avatar" role="img" aria-label="Porträtfoto"></div><div class="name">Tobias Kranzl</div><div class="role">Assembly / Montage</div></div>
    <div class="member"><div class="avatar" role="img" aria-label="Porträtfoto"></div><div class="name">Jonas Pichler</div><div class="role">Assembly / Montage</div></div>
    <div class="member"><svg class="avatar" viewBox="0 0 108 108" style="background:#c8c8c8" aria-label="Platzhalter ohne Foto"><circle cx="54" cy="40" r="20" fill="none" stroke="#d9251d" stroke-width="6"/><path d="M14 96a44 30 0 0 1 80 0" fill="none" stroke="#d9251d" stroke-width="6"/></svg><div class="name">Simon Aigner</div><div class="role">Assembly / Montage</div></div>
  </div>
</section>

<footer class="site-footer">
  <div class="footer-col" style="left:75px"><h3>Home</h3><ul><li>Über KLR</li><li>Kunden</li><li>Mission</li><li>Team</li></ul></div>
  <div class="footer-col" style="left:216px"><h3>Leistungen</h3><ul><li>Industrieanlagenbau</li><li>Reinraumtechnik</li><li>Gasversorgungsanlagen</li><li>Sondermaschinenbau</li><li>Produkte</li><li>Projekt-Management</li><li>Behörden-Management</li></ul></div>
  <div class="footer-col" style="left:440px"><h3>Jobs &amp; Karriere</h3><ul><li>Stellenangebote</li><li>Arbeiten bei KLR</li></ul></div>
  <div class="footer-col" style="left:634px"><h3>Kundenportal</h3><ul><li>Link zu NAS</li></ul></div>
  <div class="footer-brand">
    <div class="brand"><span class="brand-square"></span>KLR</div>
    <p><strong>Standort Almfeld</strong><br>Lindenweg 12<br>A-5190 Almfeld<br>Telefon: +43 (0) 123456-0</p>
    <p><strong>Standort Steinbrunn</strong><br>Mühlgasse 45<br>A-2370 Steinbrunn<br>Telefon: +43 (0) 123456-0</p>
  </div>
  <div class="footer-bottom"><span>© KLR Services GmbH 2021</span><a href="#">Impressum</a><a href="#">AGB</a><a href="#">Datenschutz</a><a href="#">Nachhaltigkeit</a></div>
</footer>
</body>
</html>
```